Velmarotix - world unique technology for better life - please let them know who am i at first sight

We need a new business card for company which is a provider of unique crystal based technology suitable for all living being. For more information and final design you can use our brochure (our colours are black and blue from brochure).
We use Verdana font

Industry/Entity Type

Business

Contact Information for Business Card

regular dimension

Font styles to use
Other font styles liked:
• Verdana

Requirements
Must have
• Logo
• name
• function/position
• phone
• mobile
• e-mail
• adress
Nice to have
• inovative design (technology directed)

```html
<!DOCTYPE html>
<html lang="en">
<head>
<meta charset="utf-8">
<title>Velmarotix business card</title>
<link rel="stylesheet" href="https://fonts.googleapis.com/css2?family=Open+Sans:wght@400;700&display=swap">
<style>
  :root {
    --backdrop: #c9c68f;
    --card-black: #050505;
    --brand-blue: #1f9bd7;
    --text-white: #f2f2f2;
    --motif-grey: #2c3437;
  }
  * { margin: 0; padding: 0; box-sizing: border-box; }
  html, body {
    width: 1200px; height: 393px; overflow: hidden;
    background: var(--backdrop);
    font-family: "Open Sans", Verdana, sans-serif;
  }
  .canvas { position: relative; width: 1200px; height: 393px; }
  .card {
    position: absolute; width: 552px; height: 315px;
    background: var(--card-black); overflow: hidden;
  }
  .card--front { left: 32px; top: 47px; }
  .card--back { left: 611px; top: 41px; }
  .motif { position: absolute; left: 0; top: 0; width: 552px; height: 315px; }

  .wordmark { position: absolute; color: var(--brand-blue); font-weight: 400; line-height: 1; }
  .wordmark__name { display: block; letter-spacing: 1px; }
  .wordmark__tag { display: block; text-transform: uppercase; }
  .card--front .wordmark { left: 22px; top: 14px; }
  .card--front .wordmark__name { font-size: 46px; }
  .card--front .wordmark__tag { font-size: 14px; letter-spacing: 16.5px; margin-top: 10px; }
  .card--back .wordmark { left: 185px; top: 112px; }
  .card--back .wordmark__name { font-size: 56px; }
  .card--back .wordmark__tag { font-size: 17px; letter-spacing: 19.5px; margin-top: 14px; }

  .holder { position: absolute; left: 22px; top: 108px; }
  .holder__name { color: var(--brand-blue); font-weight: 700; font-size: 24px; line-height: 30px; letter-spacing: 0.5px; }
  .holder__role { color: var(--text-white); font-size: 19px; line-height: 24px; }

  .contacts { position: absolute; left: 22px; top: 178px; list-style: none; }
  .contacts li {
    display: flex; align-items: center; gap: 6px;
    color: var(--text-white); font-size: 15px; height: 24px;
  }
  .contacts svg { width: 16px; height: 16px; flex: none; }
  .address { position: absolute; left: 22px; top: 283px; color: var(--text-white); font-size: 15px; }
</style>
</head>
<body>
<main class="canvas">
  <section class="card card--front">
    <svg class="motif" viewBox="0 0 552 315" role="img" aria-label="Large faint round crystal motif area">
      <circle cx="476" cy="157" r="160" fill="var(--motif-grey)"/>
    </svg>
    <div class="wordmark">
      <span class="wordmark__name">VELMAROTIX</span>
      <span class="wordmark__tag">Technologies</span>
    </div>
    <div class="holder">
      <p class="holder__name">Mirela Kostovic</p>
      <p class="holder__role">Founder and CEO</p>
    </div>
    <ul class="contacts">
      <li>
        <svg viewBox="0 0 16 16" aria-hidden="true"><circle cx="8" cy="8" r="6.5" fill="none" stroke="var(--brand-blue)" stroke-width="1.4"/><path d="M5.5 4.5l1.5 0 .6 1.8-.9.7a5 5 0 0 0 2.3 2.3l.7-.9 1.8.6v1.5c-3.5.3-6.3-2.5-6-6z" fill="var(--brand-blue)"/></svg>
        012-345-6789
      </li>
      <li>
        <svg viewBox="0 0 16 16" aria-hidden="true"><rect x="4" y="2" width="8" height="13" rx="1" fill="var(--brand-blue)"/><rect x="5.3" y="3.5" width="5.4" height="4" fill="var(--card-black)"/><rect x="9.5" y="0" width="1.2" height="3" fill="var(--brand-blue)"/></svg>
        012-345-6789
      </li>
      <li>
        <svg viewBox="0 0 16 16" aria-hidden="true"><path d="M1 6l7-4 7 4v8H1z" fill="var(--brand-blue)"/><path d="M1 6l7 5 7-5" fill="none" stroke="var(--card-black)" stroke-width="1.2"/></svg>
        info@velmarotix.com
      </li>
      <li>
        <svg viewBox="0 0 16 16" aria-hidden="true"><circle cx="8" cy="8" r="6.5" fill="var(--brand-blue)"/><g fill="none" stroke="var(--card-black)" stroke-width="0.9"><ellipse cx="8" cy="8" rx="3" ry="6.5"/><path d="M1.5 8h13M2.5 5h11M2.5 11h11M8 1.5v13"/></g></svg>
        www.velmarotix.cu
      </li>
    </ul>
    <p class="address">Street Name, City Name, Zipcode-01234</p>
  </section>

  <section class="card card--back">
    <svg class="motif" viewBox="0 0 552 315" role="img" aria-label="Large faint round crystal motif area">
      <circle cx="0" cy="157" r="160" fill="var(--motif-grey)"/>
    </svg>
    <div class="wordmark">
      <span class="wordmark__name">VELMAROTIX</span>
      <span class="wordmark__tag">Technologies</span>
    </div>
  </section>
</main>
</body>
</html>
```